business card for a massage therapy practice named 'Cedar and Willow Massage Studio'

I really need a trendy, yet easy on the eyes business card to complement my logo. Ideally with some gold or rose gold foil work.

My uploaded file of the logo I have in horizontal but I have a vertical version as well. Another color that is used in the website is a blush pink here and there. I'd like to see some trendy tropical leaves in the design.

```html
<!DOCTYPE html>
<html lang="en">
<head>
<meta charset="utf-8">
<title>Cedar and Willow Massage Studio – Business Card</title>
<link rel="stylesheet" href="https://fonts.googleapis.com/css2?family=Montserrat:wght@400;500;600&display=swap">
<style>
  :root {
    --stage: #161616;
    --paper: #f4f3f1;
    --blush: #e67f88;
    --blush-deep: #d96f79;
    --gold: #a8915c;
    --mint: #6fcdb4;
    --ink: #1c1c1c;
    --white: #ffffff;
  }
  * { box-sizing: border-box; margin: 0; padding: 0; }
  html, body { width: 1200px; height: 982px; overflow: hidden; }
  body {
    background: var(--stage);
    font-family: "Montserrat", sans-serif;
    color: var(--ink);
    position: relative;
  }
  .card {
    position: absolute;
    top: 190px;
    width: 340px;
    height: 595px;
    overflow: hidden;
    border-radius: 2px;
  }
  .card--front { left: 210px; background: var(--paper); }
  .card--back { left: 650px; background: linear-gradient(180deg, var(--blush) 0%, var(--blush-deep) 100%); }

  .brand {
    position: absolute;
    left: 0; right: 0;
    top: 62px;
    display: flex;
    flex-direction: column;
    align-items: center;
    text-align: center;
  }
  .brand__dot {
    width: 46px; height: 46px;
    border-radius: 50%;
    background: var(--gold);
    margin-bottom: 22px;
  }
  .brand__name {
    font-size: 25px;
    font-weight: 500;
    line-height: 1.25;
    color: var(--ink);
    letter-spacing: 0.5px;
  }
  .card--back .brand { top: 170px; }

  .person {
    position: absolute;
    top: 250px; left: 0; right: 0;
    text-align: center;
  }
  .person__name {
    font-size: 25px;
    font-weight: 600;
    color: var(--gold);
  }
  .person__creds {
    font-size: 12px;
    letter-spacing: 0.5px;
    margin-top: 2px;
  }
  .person__rule {
    width: 92px;
    height: 2px;
    background: var(--gold);
    margin: 8px auto 0;
  }

  .contact {
    position: absolute;
    top: 340px; left: 0; right: 0;
    list-style: none;
    text-align: center;
    font-size: 13px;
    letter-spacing: 0.3px;
  }
  .contact__item { margin-bottom: 16px; }
  .contact__icon {
    display: block;
    margin: 0 auto 6px;
    width: 16px; height: 16px;
  }

  .address {
    position: absolute;
    left: 0; right: 0; bottom: 0;
    height: 92px;
    background: var(--blush);
    display: flex;
    flex-direction: column;
    justify-content: center;
    text-align: center;
    font-size: 13px;
    line-height: 1.45;
    letter-spacing: 0.3px;
  }

  .back__web {
    position: absolute;
    left: 0; right: 0; bottom: 70px;
    text-align: center;
    color: var(--white);
    font-size: 14px;
    letter-spacing: 0.5px;
  }
</style>
</head>
<body>

<section class="card card--front" aria-label="Business card front">
  <div class="brand">
    <span class="brand__dot"></span>
    <p class="brand__name">Cedar and Willow<br>Massage Studio</p>
  </div>

  <div class="person">
    <p class="person__name">Daniel Reyes</p>
    <p class="person__creds">CLU. ChFc. RFC</p>
    <div class="person__rule"></div>
  </div>

  <ul class="contact">
    <li class="contact__item">
      <svg class="contact__icon" viewBox="0 0 16 16" aria-hidden="true">
        <path d="M3 2 L6 2 L7 5 L5.5 6.5 Q7 9.5 9.5 10.5 L11 9 L14 10 L14 13 Q13 14 11.5 14 Q5 13 2 5 Q2 3 3 2 Z" fill="var(--mint)"/>
      </svg>
      (555) 014-2087
    </li>
    <li class="contact__item">
      <svg class="contact__icon" viewBox="0 0 16 16" aria-hidden="true">
        <rect x="1" y="3" width="14" height="10" fill="var(--mint)"/>
        <path d="M1 3 L8 9 L15 3" fill="none" stroke="var(--paper)" stroke-width="1.2"/>
      </svg>
      daniel@cedarwillow-studio.com
    </li>
    <li class="contact__item">
      <svg class="contact__icon" viewBox="0 0 16 16" aria-hidden="true">
        <circle cx="8" cy="8" r="7" fill="var(--mint)"/>
        <g fill="none" stroke="var(--paper)" stroke-width="0.9">
          <ellipse cx="8" cy="8" rx="3" ry="7"/>
          <line x1="1" y1="8" x2="15" y2="8"/>
          <line x1="2.5" y1="4.5" x2="13.5" y2="4.5"/>
          <line x1="2.5" y1="11.5" x2="13.5" y2="11.5"/>
        </g>
      </svg>
      www.cedarwillow-studio.com
    </li>
  </ul>

  <address class="address" style="font-style:normal">
    <span>418 Orchard Lane</span>
    <span>Fairview, WI 53120</span>
  </address>
</section>

<section class="card card--back" aria-label="Business card back">
  <div class="brand">
    <span class="brand__dot"></span>
    <p class="brand__name">Cedar and Willow<br>Massage Studio</p>
  </div>
  <p class="back__web">www.cedar-willow.com</p>
</section>

</body>
</html>
```